Calvanto Group Real Estate Company business cards

New business card design, we are generally happy with the basic layout of the existing front of business card, (feel free to change) but require a head shot photo on the back side.

http://www.calvanto.com.au/

Attached logos, and existing business card

------------------------------

Target Market(s)

Real estate

Industry/Entity Type

Real Estate

Contact Information for Business Card

Standard size double sided

Font styles to use
Other font styles liked:
• Futura

Requirements
Must have
• Photo head shot on the back side
Nice to have
• yes
Should not have
• No

```html
<!DOCTYPE html>
<html lang="en">
<head>
<meta charset="utf-8">
<title>Calvanto Group – Business Cards</title>
<link rel="stylesheet" href="https://fonts.googleapis.com/css2?family=Open+Sans:wght@400;600;700&display=swap">
<style>
  :root {
    --backdrop: #3a3a3a;
    --card-white: #f7f7f7;
    --brand-purple: #2e1d63;
    --brand-orange: #f28c1c;
    --text-grey: #3d3d3d;
    --rule-tan: #e0b98a;
    --photo-tone: #4a3d78;
  }
  * { box-sizing: border-box; margin: 0; padding: 0; }
  html, body { width: 1200px; height: 750px; overflow: hidden; }
  body {
    background: var(--backdrop);
    font-family: "Open Sans", sans-serif;
    position: relative;
  }
  .card {
    position: absolute;
    top: 228px;
    width: 461px;
    height: 263px;
    overflow: hidden;
  }
  .card-front { left: 124px; background: var(--card-white); }
  .card-back { left: 618px; background: var(--brand-purple); }

  .brand-name {
    position: absolute;
    left: 250px;
    top: 38px;
    width: 180px;
    text-align: center;
    font-size: 38px;
    font-weight: 600;
    color: var(--brand-purple);
    letter-spacing: -0.5px;
    line-height: 1;
  }
  .tagline {
    position: absolute;
    left: 250px;
    top: 86px;
    width: 180px;
    text-align: center;
    font-size: 11px;
    font-weight: 700;
    color: var(--brand-purple);
    word-spacing: 4px;
  }
  .person-name {
    position: absolute;
    left: 24px;
    top: 137px;
    font-size: 18px;
    font-weight: 600;
    color: var(--brand-purple);
  }
  .person-title {
    position: absolute;
    left: 24px;
    top: 157px;
    font-size: 13px;
    color: var(--brand-orange);
  }
  .divider {
    position: absolute;
    left: 24px;
    top: 171px;
    width: 413px;
    height: 1px;
    background: var(--rule-tan);
  }
  .contact-list {
    position: absolute;
    left: 24px;
    top: 185px;
    list-style: none;
    font-size: 12px;
    color: var(--text-grey);
  }
  .contact-list li {
    display: flex;
    align-items: center;
    gap: 7px;
    height: 18px;
  }
  .contact-list svg { width: 11px; height: 11px; fill: var(--brand-purple); }
  .company-block {
    position: absolute;
    right: 24px;
    top: 182px;
    text-align: right;
    font-size: 12px;
    color: var(--text-grey);
    line-height: 17px;
  }
  .company-block .company-name { font-weight: 600; font-size: 13px; }
  .front-footer {
    position: absolute;
    left: 0;
    top: 238px;
    width: 461px;
    height: 25px;
  }
  .footer-url {
    position: absolute;
    right: 19px;
    top: 242px;
    font-size: 12px;
    letter-spacing: 1px;
    color: #ffffff;
  }

  .headshot {
    position: absolute;
    left: 38px;
    top: 12px;
    width: 180px;
    height: 251px;
    background: linear-gradient(180deg, var(--photo-tone) 0%, #1f2a4d 100%);
  }
  .back-brand {
    position: absolute;
    left: 240px;
    top: 150px;
    width: 214px;
    text-align: center;
    font-size: 40px;
    font-weight: 600;
    color: var(--brand-orange);
    line-height: 1;
  }
  .back-url {
    position: absolute;
    left: 240px;
    top: 230px;
    width: 214px;
    text-align: center;
    font-size: 12px;
    letter-spacing: 1.3px;
    color: #ffffff;
  }
</style>
</head>
<body>
  <section class="card card-front" aria-label="Business card front">
    <div class="brand-name">calvanto</div>
    <div class="tagline">Buy | Sell | Rent</div>

    <div class="person-name">Marcus Tran</div>
    <div class="person-title">Director</div>
    <div class="divider"></div>

    <ul class="contact-list">
      <li>
        <svg viewBox="0 0 24 24" aria-hidden="true"><path d="M6.6 10.8a15.1 15.1 0 0 0 6.6 6.6l2.2-2.2a1 1 0 0 1 1-.25 11.4 11.4 0 0 0 3.6.57 1 1 0 0 1 1 1V20a1 1 0 0 1-1 1A17 17 0 0 1 3 4a1 1 0 0 1 1-1h3.5a1 1 0 0 1 1 1c0 1.25.2 2.45.57 3.6a1 1 0 0 1-.25 1z"/></svg>
        0412 555 019
      </li>
      <li>
        <svg viewBox="0 0 24 24" aria-hidden="true"><path d="M2 5h20v14H2z M2 5l10 8 10-8" fill="var(--brand-purple)"/><path d="M3 6l9 7 9-7" fill="none" stroke="#fff" stroke-width="1.6"/></svg>
        marcus.tran@calvanto.com.au
      </li>
    </ul>

    <div class="company-block">
      <div class="company-name">Calvanto Group</div>
      <div>ABN: 12 345 678 901</div>
    </div>

    <svg class="front-footer" viewBox="0 0 461 25" aria-hidden="true">
      <polygon points="0,8 278,8 274,14 0,14" fill="var(--brand-orange)"/>
      <polygon points="0,19 461,19 461,25 0,25" fill="var(--brand-purple)"/>
      <polygon points="288,0 461,0 461,25 270,25" fill="var(--brand-purple)"/>
    </svg>
    <div class="footer-url">www.calvanto.com.au</div>
  </section>

  <section class="card card-back" aria-label="Business card back">
    <div class="headshot" role="img" aria-label="Head shot photo of the director in a navy suit and blue tie"></div>
    <div class="back-brand">calvanto</div>
    <div class="back-url">www.calvanto.com.au</div>
  </section>
</body>
</html>
```